Web design for business website

I need a web design for a business website for one of our clients who is specialized in alarm management software. I would like you to design 3 web pages, one for each of the 3 pages. You need to process the corporate identity of our client to the web design. This means the colors of the logo (red and black) should definitely show up on all of the 3 pages. Find the logo file for the logo of our customer. To increase readability I suggest you use a white/light background. All suggestions are welcome.

Please kindly download atttached Webdesign.zip and read the project brief first. The project brief refers to all other files of the zip file. Your design must have exactly the same structure as the wireframes.
Updates

Target Market(s)

B2B, Alarm management

Industry/Entity Type

Business

Number of Pages Required

3 page

Requirements
Must have
• The web design must have exactly the same structure as the wireframes and needs to contain the colors of the company logo.

```html
<!DOCTYPE html>
<html lang="en">
<head>
<meta charset="utf-8">
<title>Veranix – Real-time reasoning solutions</title>
<link href="https://fonts.googleapis.com/css2?family=Open+Sans:wght@400;600;700&family=Raleway:wght@500;600;700;800&display=swap" rel="stylesheet">
<style>
:root{
  --accent:#e8461a;
  --ink:#1d1d1d;
  --topbar:#121212;
  --nav:#1c1a33;
  --light:#f5f5f5;
  --grey:#cfcfcf;
  --muted:#6e6e6e;
  --footer:#161616;
  --footer-bottom:#111;
}
*{margin:0;padding:0;box-sizing:border-box}
html,body{width:689px;height:1200px;overflow:hidden}
body{font-family:"Open Sans",sans-serif;color:var(--ink);background:#fff;position:relative}
.abs{position:absolute}
.topbar{left:0;top:0;width:689px;height:19px;background:var(--topbar);color:#bbb;font-size:7px}
.topbar .phone{left:56px;top:5px;display:flex;gap:5px;align-items:center}
.lang{left:565px;top:0;width:67px;height:19px;border:1px solid #444;display:flex}
.lang span{display:flex;align-items:center;justify-content:center;border-right:1px solid #444;font-size:6.5px;color:#bbb}
.header{left:0;top:19px;width:689px;height:50px;background:#fff}
.brand{left:56px;top:12px;display:flex;align-items:center;gap:8px}
.brand .mark{width:26px;height:26px;border-radius:50%;background:var(--accent)}
.brand .name{font-family:"Raleway",sans-serif;font-weight:800;font-size:19px;letter-spacing:1px;line-height:1}
.brand .tag{font-size:5.5px;color:#444;margin-top:1px}
.hbtn{top:13px;width:39px;height:24px;background:var(--grey);display:flex;align-items:center;justify-content:center}
.hbtn.primary{background:var(--accent)}
.nav{left:0;top:69px;width:689px;height:24px;background:var(--nav)}
.nav a{position:absolute;top:0;height:24px;line-height:24px;color:#fff;font-size:6.5px;font-weight:600;text-decoration:none}
.nav a.active{background:var(--accent);width:50px;text-align:center}
.hero{left:0;top:93px;width:689px;height:246px;background:linear-gradient(180deg,#3a3c3e 0%,#55524a 45%,#3d3b36 100%)}
.hero::after{content:"";position:absolute;inset:0;background:rgba(20,20,25,.35)}
.hero-content{left:0;top:72px;width:689px;text-align:center;z-index:2;color:#fff}
.welcome{display:flex;justify-content:center;align-items:baseline;gap:4px;font-family:"Raleway",sans-serif}
.welcome .pre{font-size:13px;font-weight:500}
.welcome .big{font-size:30px;font-weight:800;color:var(--accent);letter-spacing:.5px}
.welcome .post{font-size:8.5px;font-family:"Open Sans",sans-serif}
.hero-content p{font-size:6.8px;line-height:10px;width:340px;margin:8px auto 0;color:#e6e6e6}
.hero .btn{left:305px;top:150px;width:78px;height:24px;background:#f2f2f2;color:#333;font-size:6.5px;font-weight:600;display:flex;align-items:center;justify-content:center;z-index:2}
.arrow{top:101px;width:30px;height:28px;display:flex;align-items:center;justify-content:center;z-index:2}
.arrow.left{left:27px;background:#fff}
.arrow.right{left:632px;background:var(--accent)}
.intro{left:0;top:372px;width:689px;color:var(--ink)}
.about{left:0;top:442px;width:689px;height:246px;background:var(--light)}
.about h2{position:absolute;left:57px;top:36px;font-family:"Raleway",sans-serif;font-weight:700;font-size:18px;color:var(--accent)}
.about p{position:absolute;left:57px;width:278px;font-size:6.4px;line-height:9.8px;color:#555}
.about .btn{position:absolute;left:57px;top:188px;width:78px;height:26px;background:var(--accent);color:#fff;font-size:6.5px;font-weight:700;display:flex;align-items:center;justify-content:center;box-shadow:0 2px 0 #b93410}
.about .photo{position:absolute;left:352px;top:0;width:280px;height:246px;background:linear-gradient(160deg,#8aa3b8 0%,#5d7388 40%,#2a3550 75%,#1e2540 100%)}
.clients-head{left:0;top:724px;width:689px;text-align:center}
.clients-head h3{font-family:"Raleway",sans-serif;font-weight:700;font-size:13.5px;color:var(--accent)}
.clients-head .rule{width:250px;height:1px;background:#ccc;margin:3px auto 5px}
.clients-head p{font-size:8px;color:var(--muted)}
.clients{left:0;top:788px;width:689px;height:50px;border-top:1px solid #ddd;border-bottom:1px solid #ddd}
.client{position:absolute;top:17px;transform:translateX(-50%);font-size:10px;font-weight:600;color:#555;display:flex;align-items:center;gap:4px;white-space:nowrap}
.client i{width:8px;height:8px;background:#999;display:block}
.social-band{left:0;top:880px;width:689px;height:125px;background:linear-gradient(180deg,#2a2a2c,#3a3631 60%,#2a2826)}
.social-band h4{position:absolute;top:32px;font-family:"Raleway",sans-serif;font-weight:600;font-size:17px;color:var(--accent)}
.soc{position:absolute;top:65px;width:25px;height:24px;background:#8a8a8a}
.soc.first{background:#3b5a9a}
.subscribe{position:absolute;left:254px;top:65px;width:378px;height:24px;border:1px solid #fff;background:#111;display:flex}
.subscribe span{flex:1;color:#ddd;font-size:6.5px;padding-left:13px;line-height:22px}
.subscribe b{width:68px;background:#fff;color:var(--accent);font-size:6.5px;text-align:center;line-height:22px}
.footer{left:0;top:1005px;width:689px;height:165px;background:var(--footer)}
.col{position:absolute;top:36px}
.col h5{font-family:"Raleway",sans-serif;font-weight:600;font-size:8px;color:#3c3c3c;margin-bottom:8px}
.col li{list-style:none;font-size:6.4px;line-height:11px;color:#4d4d4d}
.col li.hl{color:var(--accent)}
.col li svg{vertical-align:-1px;margin-right:8px}
.col li.gap{line-height:16px}
.copy{left:0;top:1170px;width:689px;height:30px;background:var(--footer-bottom);border-top:1px solid #262626;text-align:center;line-height:30px;font-size:5.5px;color:#444}
.copy b{color:var(--accent);font-weight:600}
</style>
</head>
<body>

<div class="abs topbar">
  <div class="abs phone"><svg width="7" height="7" viewBox="0 0 10 10"><path d="M2 1l2 2-1 1.5c.6 1.2 1.3 1.9 2.5 2.5L7 6l2 2-1.5 1.5C4 9 1 6 .5 2.5z" fill="#bbb"/></svg>+31 (0)20 555 0147</div>
  <div class="abs lang">
    <span style="width:20px"><svg width="6" height="4" viewBox="0 0 6 4"><path d="M0 0h6L3 4z" fill="#bbb"/></svg></span>
    <span style="width:27px">ENG</span>
    <span style="width:20px;border:none"><svg width="7" height="7" viewBox="0 0 10 10"><circle cx="4" cy="4" r="3" stroke="#bbb" stroke-width="1.5" fill="none"/><path d="M6.5 6.5L9 9" stroke="#bbb" stroke-width="1.5"/></svg></span>
  </div>
</div>

<header class="abs header">
  <div class="abs brand">
    <div class="mark"></div>
    <div><div class="name">VERANIX</div><div class="tag">Real-time reasoning solutions</div></div>
  </div>
  <div class="abs hbtn primary" style="left:504px"><svg width="8" height="8" viewBox="0 0 10 10"><circle cx="5" cy="3" r="2.3" fill="#fff"/><path d="M1 10c0-3 2-4.5 4-4.5S9 7 9 10z" fill="#fff"/></svg></div>
  <div class="abs hbtn" style="left:549px"><svg width="8" height="8" viewBox="0 0 10 10"><rect x="1" y="5" width="6" height="5" fill="#666"/><path d="M3 5V3a2 2 0 014 0" stroke="#666" fill="none" stroke-width="1.3"/></svg></div>
  <div class="abs hbtn" style="left:593px"><svg width="8" height="8" viewBox="0 0 10 10"><path d="M1 4h4V2l3 3-3 3V6H1z" fill="#666"/><path d="M6 1h3v8H6" stroke="#666" fill="none"/></svg></div>
</header>

<nav class="abs nav">
  <a class="active" style="left:56px">HOME</a>
  <a style="left:128px">INDUSTRY</a>
  <a style="left:197px">TELECOM</a>
  <a style="left:263px">POWER</a>
  <a style="left:322px">UTILITIES</a>
  <a style="left:389px">INFRA</a>
  <a style="left:443px">STORE</a>
</nav>

<section class="abs hero" role="img" aria-label="Industrial refinery pipework at dusk">
  <div class="abs hero-content">
    <div class="welcome"><span class="pre">WELCOME TO</span><span class="big">VERANIX</span><span class="post">Real-time reasoning solutions</span></div>
    <p>Companies have invested to get data out of processes. New technologies have been developed to get real-time data out of the harshest places, like oil-well drill heads or the Great Barrier Riff.</p>
  </div>
  <div class="abs btn">LEARN MORE</div>
  <div class="abs arrow left"><svg width="6" height="8" viewBox="0 0 6 8"><path d="M5 1L2 4l3 3" stroke="#222" stroke-width="1.6" fill="none"/></svg></div>
  <div class="abs arrow right"><svg width="6" height="8" viewBox="0 0 6 8"><path d="M1 1l3 3-3 3" stroke="#fff" stroke-width="1.6" fill="none"/></svg></div>
</section>

<section class="abs intro">
  <div class="welcome"><span class="pre">WELCOME TO</span><span class="big">VERANIX</span><span class="post">Real-time reasoning solutions</span></div>
</section>

<section class="abs about">
  <h2>ABOUT US</h2>
  <p style="top:68px">Companies have invested to get data out of processes. New technologies have been developed to get real-time data out of the harshest places, like oil-well drill heads or the Great Barrier Riff. Data in itself means nothing without the context the data is collected in. Example: data from equipment under maintenance does not provide information to operations. Information - data which is valid and meaningful can overwhelm any user without the proper knowledge to interpret this information.</p>
  <p style="top:136px">Veranix technology enables easy application of such knowledge in a comprehensible – visual – representation and makes hypothetical reasoning with information possible providing meaningful advisories to subscribers when they need it or when it is required that they are made aware of a situation which requires their attention.</p>
  <div class="btn">LEARN MORE</div>
  <div class="photo" role="img" aria-label="Two engineers in hard hats inspecting equipment among steel pipework"></div>
</section>

<section class="abs clients-head">
  <h3>CLIENTS THAT TRUST US</h3>
  <div class="rule"></div>
  <p>Some of our clients that trust us, be shure to be one of them.</p>
</section>

<section class="abs clients">
  <div class="client" style="left:98px">Corvane</div>
  <div class="client" style="left:182px">Halbrook</div>
  <div class="client" style="left:266px">Ostera</div>
  <div class="client" style="left:341px">Quillon</div>
  <div class="client" style="left:424px">Brouwmark</div>
  <div class="client" style="left:508px">Petrava</div>
  <div class="client" style="left:590px"><i></i>Nordhaven</div>
</section>

<section class="abs social-band">
  <h4 style="left:56px">FOLLOW US ON :</h4>
  <div class="soc first" style="left:56px" aria-label="Social network 1"></div>
  <div class="soc" style="left:86px" aria-label="Social network 2"></div>
  <div class="soc" style="left:117px" aria-label="Social network 3"></div>
  <div class="soc" style="left:147px" aria-label="Social network 4"></div>
  <div class="soc" style="left:177px" aria-label="Social network 5"></div>
  <h4 style="left:253px">SUBSCRIBE NOW :</h4>
  <div class="subscribe"><span>Enter Your Email Adress</span><b>SUBSCRIBE</b></div>
</section>

<footer class="abs footer">
  <div class="col" style="left:56px"><h5>SOLUTIONS</h5><ul><li class="hl">Sentra Alarm Reporting</li><li>Sentra Alarm Analysis</li><li>Sentra Alarm Expert</li><li>USE</li></ul></div>
  <div class="col" style="left:154px"><h5>INDUSTRIES</h5><ul><li>Industry</li><li>Telecom</li><li>Power</li><li>Utilites</li><li>Infra</li></ul></div>
  <div class="col" style="left:254px"><h5>ABOUT US</h5><ul><li>Company</li><li>Overview</li><li>Leadership</li><li>Partners</li><li>Locations</li></ul></div>
  <div class="col" style="left:352px"><h5>NEWS</h5><ul><li>Product News</li><li>Partner News</li><li>Events</li><li>Press Releases</li><li>Vacancies</li></ul></div>
  <div class="col" style="left:500px"><h5>CONTACT US</h5><ul>
    <li class="gap"><svg width="6" height="6" viewBox="0 0 10 10"><path d="M2 1l2 2-1 1.5c.6 1.2 1.3 1.9 2.5 2.5L7 6l2 2-1.5 1.5C4 9 1 6 .5 2.5z" fill="#4d4d4d"/></svg>+31 (0)20 555 0147</li>
    <li class="gap"><svg width="6" height="6" viewBox="0 0 10 8"><rect width="10" height="8" fill="#4d4d4d"/><path d="M0 0l5 4 5-4" stroke="#161616" fill="none"/></svg>hello@veranix.example</li>
    <li class="gap"><svg width="6" height="6" viewBox="0 0 10 10"><path d="M5 0a3.5 3.5 0 013.5 3.5C8.5 6 5 10 5 10S1.5 6 1.5 3.5A3.5 3.5 0 015 0z" fill="#4d4d4d"/></svg>address Veranix Leiden</li>
  </ul></div>
</footer>

<div class="abs copy">Copyright © 2105 <b>VERANIX.</b> All Rights Reserved.</div>

</body>
</html>
```